Business card design for a dynamic IT consulting company

We need a business card design for a young firm, specialized in the Telecommunications/Consulting industry. The name of the company is Quindor and Partners Business Consulting Ltd. (Short name: Quindor and Partnes)
Quindor = solve read reverse, so we aim to be uncomplicated and solution-oriented. The small pipe in our logo is also related to the word solve. So we need a new business card design, which is simple, eye catching and something non traditional (I would probably prefer a square shaped design rather than a rectangle, but open for suggestions). Attached our logo.

Target Market(s)

Usually our customers are Tier1 Telecoms providers (Q-Netra, Palorix, etc) and their executives.

Industry/Entity Type

Business

Contact Information for Business Card

Name: Bence Tolnavari
Email: b.tolnavari@quindor.hu
Web: www.quindor.hu
Mobile: +36 30 518 2769
Title: Managing Director

Optional:
Company name: Quindor and Partners Ltd.
Address: 1087 Budapest, Tolvenka str. 28/C, Hungary

Font styles to use
Other font styles liked:
• helveticaneue_medium, Prime Regular are used now.

Colors

Designer to choose colors to be used in the design.

Requirements
Must have
• I would like to have a 2 sided design.
Nice to have
• I thought if we make the logo a bit bigger (without the company name), that could go to the back with the company name below. I though, if the pipe in the logo is somehow touchable on the business card, would be nice and unique.

```html
<!DOCTYPE html>
<html lang="en">
<head>
<meta charset="utf-8">
<title>Quindor and Partners – Business Card</title>
<link rel="stylesheet" href="https://fonts.googleapis.com/css2?family=Quicksand:wght@400&family=Saira+Condensed:wght@600&family=Saira:wght@500&family=Work+Sans:wght@400&display=swap">
<style>
  :root {
    --backdrop: #1b1b1b;
    --card: #262626;
    --card-edge: #303030;
    --silver: #bdbdbd;
    --white: #e8e8e8;
    --blue: #1a9ad6;
    --magenta: #b0307f;
  }
  * { margin: 0; padding: 0; box-sizing: border-box; }
  html, body { width: 1200px; height: 900px; overflow: hidden; background: var(--backdrop); }
  .canvas { position: relative; width: 1200px; height: 900px; }
  .card {
    position: absolute; left: 250px; width: 700px; height: 400px;
    background: linear-gradient(135deg, var(--card-edge), var(--card) 60%);
    box-shadow: 0 12px 30px rgba(0,0,0,.55);
  }
  .card--front { top: 35px; }
  .card--back { top: 465px; }

  .brand {
    position: absolute; left: 0; right: 0; top: 150px;
    display: flex; align-items: center; justify-content: center; gap: 18px;
  }
  .brand__square { width: 34px; height: 34px; background: var(--silver); }
  .brand__name {
    font-family: "Quicksand", sans-serif; font-weight: 400;
    font-size: 54px; line-height: 1.2; color: var(--silver); letter-spacing: 1px;
  }
  .front__url {
    position: absolute; left: 0; right: 0; bottom: 40px; text-align: center;
    font-family: "Work Sans", sans-serif; font-size: 17px; letter-spacing: 3px; color: var(--white);
  }

  .person {
    position: absolute; right: 385px; top: 135px; text-align: right;
  }
  .person__name {
    font-family: "Saira Condensed", sans-serif; font-weight: 600;
    font-size: 42px; line-height: 1; color: var(--blue); letter-spacing: .5px;
    white-space: nowrap;
  }
  .person__title {
    margin-top: 8px; font-family: "Work Sans", sans-serif; font-size: 17px;
    letter-spacing: 1px; color: var(--white); white-space: nowrap;
  }
  .divider {
    position: absolute; left: 338px; top: 140px; width: 2px; height: 74px; background: var(--magenta);
  }
  .contacts {
    position: absolute; left: 362px; top: 143px; list-style: none;
    font-family: "Work Sans", sans-serif; font-size: 17px; color: var(--white);
  }
  .contacts li { display: flex; align-items: center; gap: 14px; height: 23px; white-space: nowrap; }
  .contacts svg { width: 15px; height: 15px; fill: var(--blue); flex: none; }
  .address {
    position: absolute; left: 40px; right: 30px; bottom: 55px; white-space: nowrap;
    font-family: "Work Sans", sans-serif; font-size: 16px; color: var(--white); letter-spacing: .3px;
  }
  .address__company {
    font-family: "Saira", sans-serif; font-weight: 500; color: var(--blue); letter-spacing: .5px;
  }
</style>
</head>
<body>
<div class="canvas">
  <section class="card card--front">
    <div class="brand">
      <span class="brand__square"></span>
      <span class="brand__name">Quindor &amp; Partners</span>
    </div>
    <p class="front__url">www.quindor.hu</p>
  </section>

  <section class="card card--back">
    <div class="person">
      <h1 class="person__name">BENCE TOLNAVARI</h1>
      <p class="person__title">MANAGING DIRECTOR</p>
    </div>
    <span class="divider"></span>
    <ul class="contacts">
      <li>
        <svg viewBox="0 0 24 24"><path d="M6.6 10.8c1.4 2.8 3.8 5.1 6.6 6.6l2.2-2.2c.3-.3.7-.4 1-.2 1.1.4 2.3.6 3.6.6.6 0 1 .4 1 1V20c0 .6-.4 1-1 1C10.6 21 3 13.4 3 4c0-.6.4-1 1-1h3.5c.6 0 1 .4 1 1 0 1.3.2 2.5.6 3.6.1.3 0 .7-.2 1z"/></svg>
        +36 30 518 2769
      </li>
      <li>
        <svg viewBox="0 0 24 24"><path d="M2 5h20v14H2z M2 5l10 8 10-8" stroke="#262626" stroke-width="1.5"/></svg>
        b.tolnavari@quindor.hu
      </li>
      <li>
        <svg viewBox="0 0 24 24"><path d="M12 2a10 10 0 100 20 10 10 0 000-20zm6.9 6h-3a15 15 0 00-1.3-3.9A8 8 0 0118.9 8zM12 4c.8 1.2 1.5 2.5 1.9 4h-3.8c.4-1.5 1.1-2.8 1.9-4zM4.3 14a8 8 0 010-4h3.4a17 17 0 000 4zm.8 2h3a15 15 0 001.3 3.9A8 8 0 015.1 16zm3-8h-3a8 8 0 014.3-3.9A15 15 0 008.1 8zM12 20c-.8-1.2-1.5-2.5-1.9-4h3.8c-.4 1.5-1.1 2.8-1.9 4zm2.3-6H9.7a15 15 0 010-4h4.6a15 15 0 010 4zm.3 5.9a15 15 0 001.3-3.9h3a8 8 0 01-4.3 3.9zm1.7-5.9a17 17 0 000-4h3.4a8 8 0 010 4z"/></svg>
        www.quindor.hu
      </li>
    </ul>
    <p class="address"><span class="address__company">QUINDOR AND PARTNERS LTD:</span> 1087 Budapest, Tolvenka str. 28/C, Hungary</p>
  </section>
</div>
</body>
</html>
```